Cleaning service website design

We need a new nice web design(logo will be the same) for a new cleaning service Company:

Informations about Company and logo you can take from flyers in attachments.

This is a cleaning service Company which have simple rules and we would like to show that(in checklist form) on website:

- What we do and that we're Cleaning Green

- Why us?

- How much(our pricing is simple)

Also we would like to communicate with clients by some nice/big pictures on website and the most important thing is our phone number and short/fast Brimtallow.

Also there should be some space for description about our Company.

Generally all information on main page can be short: about us, about service(what we do), last reviews, tips (for example: Tip of the week) and other can be some introduction to subpage where will be more information.

There will be few subpages like: About us, About our service, Photos(Before and after), Reviews , Tips, FAQ, Contact, Looking for a Job? - most of them will be just text so you can project just one example.

```html
<!DOCTYPE html>
<html lang="en">
<head>
<meta charset="utf-8">
<title>Tidy Nest – Cleaning Service</title>
<link href="https://fonts.googleapis.com/css2?family=Ubuntu:wght@400;500&family=Open+Sans:wght@300;400&display=swap" rel="stylesheet">
<style>
:root{
  --green:#5aaa3c;
  --green-dark:#3f8a26;
  --green-light:#7cc35a;
  --blue:#1a5fb0;
  --blue-dark:#0e4a98;
  --sky:#e4eef8;
  --heading:#2e2e2e;
  --text:#6b6b6b;
  --tip-blue:#1b6bb5;
  --orange:#e0742a;
  --footer:#2b2b2b;
  --line:#d8e2ec;
}
*{margin:0;padding:0;box-sizing:border-box}
html,body{width:802px;height:1200px;overflow:hidden;background:#fff}
body{position:relative;font-family:'Open Sans',sans-serif;color:var(--text)}
.sky-band{position:absolute;left:0;top:0;width:802px;height:306px;background:linear-gradient(#f6f9fd,var(--sky))}
.abs{position:absolute}

.brand{left:64px;top:14px;width:134px;height:78px;display:flex;align-items:center;gap:6px}
.brand-dot{width:16px;height:16px;border-radius:50%;background:var(--green)}
.brand-name{font-family:'Ubuntu',sans-serif;font-weight:500;font-size:22px;color:var(--blue)}

.call{right:58px;top:24px;text-align:left;font-family:'Ubuntu',sans-serif;color:var(--blue-dark)}
.call small{display:block;font-size:12px}
.call strong{display:block;font-size:18px;font-weight:500;letter-spacing:.3px}
.search{left:574px;top:66px;width:172px;height:21px;border:1px solid #d6dde4;background:#fff;font-size:8.5px;font-style:italic;color:#999;padding:4px 8px}
.search svg{position:absolute;right:7px;top:4px}

.nav{left:50px;top:98px;width:702px;height:39px;border-radius:4px;background:linear-gradient(var(--green-light),var(--green) 55%,var(--green-dark));display:flex;align-items:center}
.nav a{flex:none;display:block;font-family:'Ubuntu',sans-serif;font-size:12px;color:#fff;text-decoration:none;text-align:center;white-space:nowrap;line-height:39px;height:39px;border-right:1px solid rgba(0,0,0,.15)}
.nav a:last-child{border:0}

.hero{left:50px;top:142px;width:702px;height:248px;background:var(--blue);border-radius:6px 6px 10px 10px;padding:7px}
.hero-photo{width:100%;height:228px;border-radius:4px;background:linear-gradient(100deg,#f4f2ee 0%,#e9e6df 40%,#eef0f2 70%,#d9e3ef 100%)}
.dots{left:368px;top:364px;display:flex;gap:3px}
.dots i{width:8px;height:8px;border-radius:50%;background:#222}

h1.welcome{left:51px;top:406px;font-family:'Ubuntu',sans-serif;font-weight:400;font-size:18px;color:var(--heading)}
.team{left:50px;top:432px;width:188px;height:107px;background:linear-gradient(90deg,#efe2cf,#d8c0a0 50%,#e9e4dc)}
.intro{left:252px;top:443px;width:276px;font-size:8.6px;line-height:16.8px;font-weight:300}

h2.do-title{left:49px;top:566px;font-family:'Ubuntu',sans-serif;font-weight:400;font-size:16px;color:var(--green-dark)}
.do-text{left:49px;top:590px;width:480px;font-size:8.6px;line-height:16.8px;font-weight:300}
.checklist{left:48px;top:636px;width:460px;display:grid;grid-template-columns:236px 224px;row-gap:9px}
.checklist li{list-style:none;display:flex;align-items:center;gap:8px;font-family:'Ubuntu',sans-serif;font-size:9.6px;color:#333;height:19px;white-space:nowrap;background:linear-gradient(90deg,#fff,#f1f1f1 70%,#fff)}

.form{left:546px;top:402px;width:202px;height:332px;border:1px solid #dfe4ea;border-radius:4px;background:#fff}
.form h3{height:35px;background:linear-gradient(#2b7ccd,var(--blue-dark));border-radius:4px 4px 0 0;font-family:'Ubuntu',sans-serif;font-weight:400;font-size:14px;color:#fff;padding:8px 18px;white-space:nowrap}
.field{position:absolute;left:13px;width:177px;height:22px;border:1px solid #d3d8de;font-size:8.6px;color:#666;padding:5px 10px}
.field.msg{height:85px}
.submit{position:absolute;left:120px;top:292px;width:69px;height:24px;background:linear-gradient(#243040,#0f1720);border-radius:3px;color:#fff;font-family:'Ubuntu',sans-serif;font-size:9.6px;text-align:center;line-height:24px}

.divider{left:51px;top:758px;width:702px;height:1px;background:#e6e6e6}
.vline{left:256px;top:776px;width:1px;height:270px;background:#e6e6e6}

h2.tips-title{left:49px;top:780px;font-family:'Ubuntu',sans-serif;font-weight:400;font-size:17px;color:var(--tip-blue)}
.tip{left:50px;width:190px;font-size:8.6px;line-height:13.6px;font-weight:300}
.tip h4{font-family:'Ubuntu',sans-serif;font-weight:400;font-size:10.4px;color:var(--tip-blue);margin-bottom:2px}
.tip-sep{left:50px;width:190px;height:2px;background:var(--line)}

h2.rev-title{left:276px;top:780px;font-family:'Ubuntu',sans-serif;font-weight:400;font-size:17px;color:var(--orange)}
.review{left:276px;width:470px;display:flex;gap:13px}
.review .pic{flex:none;width:97px;height:64px}
.review h4{font-family:'Ubuntu',sans-serif;font-weight:400;font-size:10.4px;color:#333;margin-bottom:2px}
.review p{font-size:8.6px;line-height:16.8px;font-weight:300}

.footer{left:0;top:1088px;width:802px;height:112px}
.footer-links{left:56px;top:1131px;font-family:'Ubuntu',sans-serif;font-size:9.8px;color:#fff;white-space:nowrap}
.footer-links span{margin:0 4px;color:#ccc}
.copyright{left:56px;top:1152px;font-size:7.8px;color:#bbb}
.social{left:688px;top:1129px;display:flex;gap:4px}
.social i{width:18px;height:18px;border-radius:3px;background:#4b8fd6}
</style>
</head>
<body>
<div class="sky-band"></div>

<header>
  <div class="abs brand"><span class="brand-dot"></span><span class="brand-name">Tidy Nest</span></div>
  <div class="abs call"><small>Call Us Today</small><strong>555-204-7731</strong></div>
  <div class="abs search">Search here..
    <svg width="12" height="12" viewBox="0 0 12 12"><circle cx="5" cy="5" r="3.6" fill="none" stroke="#888" stroke-width="1.6"/><line x1="7.6" y1="7.6" x2="11" y2="11" stroke="#888" stroke-width="1.8"/></svg>
  </div>
  <nav class="abs nav">
    <a style="width:64px">Home</a><a style="width:73px">About Us</a><a style="width:82px">Our Service</a><a style="width:100px">Photos Gallery</a><a style="width:66px">Reviews</a><a style="width:46px">Tips</a><a style="width:47px">FAQ</a><a style="width:64px">Contact</a><a style="width:160px">Looking for a Job?</a>
  </nav>
</header>

<section class="abs hero">
  <div class="hero-photo" role="img" aria-label="Cleaner in yellow gloves wiping a bright kitchen counter next to a bucket of cleaning supplies"></div>
</section>
<div class="abs dots"><i></i><i></i><i></i><i></i></div>

<h1 class="abs welcome">Welcome to Our Website Mainpage..</h1>
<div class="abs team" role="img" aria-label="Team of four cleaners in gloves giving a thumbs up"></div>
<p class="abs intro">We are Daniel and Marta Kowerski and we have personally experienced the struggle of finding a reliable and affordable maid service. We understand how busy life can be and cleaning is one of the tasks that falls off the list when you're stretched too thin. We are here to help! Let Tidy Nest take care of the house cleaning so you can focus on the more important things in life. Westbrook.</p>

<h2 class="abs do-title">What We Do</h2>
<p class="abs do-text">Nunc tempus felis vitae urna. Vivamus porttitor, g, purus nisi eleifend libero, a tempus libero lectus feugiat felis. Morbi diam mauris, viverra in, gravida eu, mattis in, ante. Morbi eget arcu.</p>
<ul class="abs checklist">
  <li><svg width="18" height="16" viewBox="0 0 18 16"><circle cx="9" cy="8" r="7" fill="#222"/><path d="M5 8.2l2.6 2.6L13 5.4" fill="none" stroke="#fff" stroke-width="1.8"/></svg>Etiam est nunc venenatis in</li>
  <li><svg width="18" height="16" viewBox="0 0 18 16"><circle cx="9" cy="8" r="7" fill="#222"/><path d="M5 8.2l2.6 2.6L13 5.4" fill="none" stroke="#fff" stroke-width="1.8"/></svg>Dis parturient montes nascetur</li>
  <li><svg width="18" height="16" viewBox="0 0 18 16"><circle cx="9" cy="8" r="7" fill="#222"/><path d="M5 8.2l2.6 2.6L13 5.4" fill="none" stroke="#fff" stroke-width="1.8"/></svg>Tristique eu, imperdiet ac nisl.</li>
  <li><svg width="18" height="16" viewBox="0 0 18 16"><circle cx="9" cy="8" r="7" fill="#222"/><path d="M5 8.2l2.6 2.6L13 5.4" fill="none" stroke="#fff" stroke-width="1.8"/></svg>In iaculis facilisis massa.</li>
  <li><svg width="18" height="16" viewBox="0 0 18 16"><circle cx="9" cy="8" r="7" fill="#222"/><path d="M5 8.2l2.6 2.6L13 5.4" fill="none" stroke="#fff" stroke-width="1.8"/></svg>Cum sociis natoque penatibus et magnis</li>
  <li><svg width="18" height="16" viewBox="0 0 18 16"><circle cx="9" cy="8" r="7" fill="#222"/><path d="M5 8.2l2.6 2.6L13 5.4" fill="none" stroke="#fff" stroke-width="1.8"/></svg>Suspendisse quam leo molestie sed</li>
</ul>

<aside class="abs form">
  <h3>Fill Our Contact Form</h3>
  <div class="field" style="top:45px">Full Name</div>
  <div class="field" style="top:76px">Last Name</div>
  <div class="field" style="top:106px">City/Zipcode</div>
  <div class="field" style="top:137px">Email address</div>
  <div class="field" style="top:167px">Phone no.</div>
  <div class="field msg" style="top:199px">Message/Comments</div>
  <div class="submit">SUBMIT</div>
</aside>

<div class="abs divider"></div>
<div class="abs vline"></div>

<h2 class="abs tips-title">Tips of the Week</h2>
<div class="abs tip" style="top:814px"><h4>Vestibulum ligula augue</h4>Mauris vel lacus vitae felis vestibulum volutpat. Etiam est nunc venenatis</div>
<div class="abs tip-sep" style="top:867px"></div>
<div class="abs tip" style="top:877px"><h4>Donec scelerisque leo</h4>Mauris vel lacus vitae felis vestibulum volutpat.</div>
<div class="abs tip-sep" style="top:918px"></div>
<div class="abs tip" style="top:928px"><h4>Ut nisi erat</h4>Vitae felis vestibulum volutpat. Etiam est nunc</div>
<div class="abs tip-sep" style="top:967px"></div>
<div class="abs tip" style="top:978px"><h4>Vestibulum ligula augue</h4>Mauris vel lacus vitae felis vestibulum</div>

<h2 class="abs rev-title">Latest Reviews</h2>
<article class="abs review" style="top:813px">
  <div class="pic" role="img" aria-label="Couple cleaning a kitchen together" style="background:linear-gradient(#c9ccd0,#8f969c)"></div>
  <div><h4>Duis tincidunt lectus quis</h4><p>Suspendisse vulputate aliquam dui. Nulla elementum dui ut augue. Aliquam vehicula mi at mauris. Maecenas placerat, nisl at consequat rhoncus, sem nunc gravida justo, quis eleifend arcu velit quis lacus. Morbi magna magna, tincidunt a, mattis non</p></div>
</article>
<article class="abs review" style="top:898px">
  <div class="pic" role="img" aria-label="Gloved hand wiping a counter with a blue cloth" style="background:linear-gradient(120deg,#3a62a8,#d9dfe6 55%,#f2f2f2)"></div>
  <div><h4>Duis tincidunt lectus quis</h4><p>Suspendisse vulputate aliquam dui. Nulla elementum dui ut augue. Aliquam vehicula mi at mauris. Maecenas placerat, nisl at consequat rhoncus, sem nunc gravida justo, quis eleifend arcu velit quis lacus. Morbi magna magna, tincidunt a, mattis non</p></div>
</article>
<article class="abs review" style="top:982px">
  <div class="pic" role="img" aria-label="Cleaner vacuuming a wooden floor in a warm room" style="background:linear-gradient(#d99a45,#b8621e)"></div>
  <div><h4>Duis tincidunt lectus quis</h4><p>Suspendisse vulputate aliquam dui. Nulla elementum dui ut augue. Aliquam vehicula mi at mauris. Maecenas placerat, nisl at consequat rhoncus, sem nunc gravida justo, quis eleifend arcu velit quis lacus. Morbi magna magna, tincidunt a, mattis non</p></div>
</article>

<footer>
  <svg class="abs footer" width="802" height="112" viewBox="0 0 802 112">
    <path d="M0 6 Q401 -4 802 6 V112 H0Z" fill="#cfd2d6"/>
    <path d="M0 10 Q401 0 802 10 V112 H0Z" fill="#2b2b2b"/>
  </svg>
  <div class="abs footer-links">Home<span>|</span>About Us<span>|</span>Our Service<span>|</span>Photos Gallery<span>|</span>Reviews<span>|</span>Tips<span>|</span>FAQ<span>|</span>Contact<span>|</span>Looking for a Job?</div>
  <div class="abs copyright">© 2013 Company Name. All right reserved.&nbsp; Privacy Policy</div>
  <div class="abs social" aria-label="Social links"><i></i><i></i><i></i></div>
</footer>
</body>
</html>
```